zAvora Corporate Website

zAvora is a well-funded start up developing an Online Marketing Platform for small businesses in Europe.
We are launching in February 2012 with all-in-one online marketing services including professional website, DIY SEO, Dashboard with Reports and Online marketing tools, and Support.
Our internal web designer has come up with a preliminary website design which we wish to continue to improve using new ideas, colours, layout, image, etc.
The brief is very simple - improve the website whether it is look & feel, ease of use, conversion rate - we are looking for overall improvements.
The contest will last 5 days and we will award the winner £300.
If you are the winner , you will also be required to provide designs for 3 more internal pages adhering to the proposed home page design.
Judging criteria : -
Visual Design
Layout must adhere to best practices and wire frame. If you decide to move elements around significantly please provide reason
Functional, informative and drives calls to action
Industry/Entity Type
Marketing
Look and feel
Each slider illustrates characteristics of the customer's brand and the style your logo design should communicate.

```html
<!DOCTYPE html>
<html lang="en">
<head>
<meta charset="utf-8">
<title>zAvora – Online Marketing Platform</title>
<link href="https://fonts.googleapis.com/css2?family=Noto+Sans:ital,wght@0,400;0,500;1,400&display=swap" rel="stylesheet">
<style>
:root{
  --ink:#222;
  --text:#444;
  --muted:#555;
  --accent:#3aa3c6;
  --accent-bright:#5bc8e8;
  --dark:#4b4b4b;
  --band:#e4e6e6;
  --line:#c9c9c9;
  --white:#fff;
}
*{box-sizing:border-box;margin:0;padding:0}
html,body{width:1050px;height:1200px;overflow:hidden}
body{position:relative;background:var(--white);font-family:"Noto Sans",Verdana,sans-serif;color:var(--text)}
.abs{position:absolute}
a{color:inherit}

.top-band{left:0;top:0;width:1050px;height:506px;background:linear-gradient(#fff 0,#f1f2f2 60px,#eceeee 140px,#e2e4e4 480px,#eef0f0 506px)}
.brand{left:0;top:22px;width:1050px;text-align:center;font-size:27px;color:#4a4a4a;letter-spacing:.3px}
.brand-dot{display:inline-block;width:24px;height:24px;border-radius:50%;background:var(--accent-bright);margin-right:6px;vertical-align:-3px}

.nav{left:40px;top:75px;width:970px;height:60px;background:#eceeee;background-image:radial-gradient(#dcdfdf 1px,transparent 1px);background-size:4px 4px;border-top:2px solid #d6d8d8}
.nav-item{position:absolute;top:12px;height:36px;line-height:36px;font-size:13.5px;color:var(--ink);letter-spacing:.4px}
.nav-item.is-active{left:11px;width:71px;text-align:center;background:var(--dark);color:var(--accent-bright);border-radius:5px}
.social{position:absolute;top:19px;width:24px;height:24px;border-radius:3px}

.slider{left:40px;top:150px;width:972px;height:316px;background:#f6f7f7;box-shadow:0 3px 10px rgba(0,0,0,.35)}
.slide{position:absolute;left:10px;top:9px;width:950px;height:293px;background:linear-gradient(90deg,#fbfbfb,#fff 60%,#e9eef1)}
.slide-photo{position:absolute;left:0;top:0;width:390px;height:293px;background:linear-gradient(#f3f4f5,#dcdfe1)}
.slide-title{position:absolute;left:404px;top:52px;font-size:21.5px;color:var(--ink);letter-spacing:.5px}
.slide-text{position:absolute;left:406px;top:92px;width:480px;font-size:13px;line-height:23px;letter-spacing:.3px}
.slide-more{position:absolute;left:807px;top:154px;font-size:13px;color:var(--ink);letter-spacing:.3px}
.slide-more i{display:inline-block;width:17px;height:17px;border:3px solid var(--accent-bright);border-radius:50%;margin-right:7px;vertical-align:-4px}
.slide-pager{position:absolute;left:700px;top:253px;width:250px;height:40px;background:linear-gradient(90deg,rgba(200,205,208,0),rgba(185,190,194,.85) 25%)}
.pager-dot{position:absolute;top:15px;width:11px;height:11px;border-radius:50%;background:#4a4a4a}
.pager-dot.is-current{background:var(--accent-bright);border:2px solid #3a4a50;width:14px;height:14px;top:13px}

.welcome-tab{left:40px;top:488px;width:239px;height:34px;background:var(--dark);color:var(--white);font-size:19px;line-height:34px;padding-left:20px;letter-spacing:.6px}
.welcome-photo{left:54px;top:542px;width:228px;height:138px;border:3px solid #555;border-radius:4px;background:linear-gradient(#fff,#e9e4df)}
.welcome-text{left:298px;top:553px;width:700px;font-size:12.8px;line-height:20px;text-align:justify;letter-spacing:.15px}
.welcome-text a{color:var(--accent);text-decoration:none;font-size:14.5px;margin-left:4px}
.rule{left:42px;top:700px;width:970px;border-top:1px solid var(--line)}

.section-title{font-size:17.5px;color:var(--accent);letter-spacing:.4px}
.news-item{left:42px;width:290px;font-size:12px;line-height:18px}
.news-item h4{font-weight:400;font-size:13px;color:var(--ink);padding-left:15px;position:relative;margin-bottom:1px}
.news-item h4::before{content:"";position:absolute;left:1px;top:5px;border-left:6px solid #555;border-top:4px solid transparent;border-bottom:4px solid transparent}
.news-item p{padding-left:15px}
.news-item a{color:var(--ink)}
.dash{left:42px;top:896px;width:288px;border-top:1px dashed #555}

.feature{top:718px;height:156px;background:linear-gradient(#fff,#eceeee);padding:12px 0 0 18px}
.feature h3{font-weight:400;font-style:italic;font-size:14.5px;color:var(--ink);letter-spacing:.4px}
.feature .lead{font-size:12.5px;line-height:20px;margin-top:9px;width:130px}
.feature .body{font-size:12px;line-height:19px;margin-top:12px;width:176px;text-align:justify}
.feature .body a{color:var(--ink)}
.feature-icon{position:absolute;top:8px;width:58px;height:62px;border-radius:4px}

.quote{left:42px;top:938px;width:290px;height:124px;background:var(--dark);border-radius:4px;color:var(--white);font-size:12.8px;line-height:20px;padding:20px 18px 0 14px;text-align:justify;letter-spacing:.2px}
.quote b{color:var(--accent-bright);font-size:17px;font-weight:500}
.quote-tail{left:52px;top:1061px}
.quote-name{left:84px;top:1065px;font-size:14px;color:var(--ink);letter-spacing:.5px}

.block-title{font-size:16.5px;color:var(--ink);letter-spacing:.5px}
.mail-input{left:357px;top:939px;width:212px;height:36px;background:#dcdcdc;border:1px solid #c4c4c4;font-size:13px;line-height:34px;padding-left:10px;color:#555;letter-spacing:.3px}
.subscribe{left:497px;top:986px;width:73px;height:30px;background:var(--accent-bright);border-radius:5px;box-shadow:0 2px 3px rgba(0,0,0,.3);color:#123;font-size:12px;line-height:30px;text-align:center;letter-spacing:.3px}
.mail-note{left:360px;top:1027px;width:215px;font-size:12px;line-height:18px;letter-spacing:.3px}
.v-rule{left:597px;top:913px;height:145px;border-left:1px solid #888}
.contact-line{left:620px;font-size:12px;line-height:18px;color:var(--ink);letter-spacing:.4px}
.contact-line svg{position:absolute;left:2px;top:0}
.contact-line span{display:block;padding-left:30px}
.social-art{left:830px;top:905px;width:170px;height:165px;background:radial-gradient(ellipse at 50% 45%,#e8ecef,#fff 70%)}

.footer{left:0;top:1106px;width:1050px;height:94px;background:var(--dark);color:var(--white);text-align:center;font-size:11.5px;letter-spacing:.4px}
.footer-links{padding-top:17px}
.footer-links span{margin:0 12px}
.copyright{margin-top:20px}
</style>
</head>
<body>

<div class="abs top-band"></div>
<div class="abs brand"><span class="brand-dot"></span>zAvora</div>

<nav class="abs nav">
  <span class="nav-item is-active">Home</span>
  <span class="nav-item" style="left:119px">Products</span>
  <span class="nav-item" style="left:233px">About Us</span>
  <span class="nav-item" style="left:349px">Pricing</span>
  <span class="nav-item" style="left:449px">Contactus</span>
  <span class="social" style="left:779px;background:#3b5998" aria-label="Social network"></span>
  <span class="social" style="left:819px;background:#5fc2ea" aria-label="Social network"></span>
  <span class="social" style="left:859px;background:#f07a2c" aria-label="Social network"></span>
  <span class="social" style="left:899px;background:#1f6fa8" aria-label="Social network"></span>
  <span class="social" style="left:939px;background:#e3e3e3" aria-label="Social network"></span>
</nav>

<section class="abs slider">
  <div class="slide">
    <div class="slide-photo" role="img" aria-label="Photo of a cheering man in a red shirt with a laptop"></div>
    <h1 class="slide-title" style="font-weight:400">Online Marketing Platform for Small Business</h1>
    <p class="slide-text">Get a big business website and sales tools from £19/month. It's Easy, Powerful and Low Cost.</p>
    <div class="slide-more"><i></i>View more</div>
    <div class="slide-pager">
      <span class="pager-dot is-current" style="left:108px"></span>
      <span class="pager-dot" style="left:131px"></span>
      <span class="pager-dot" style="left:152px"></span>
      <span class="pager-dot" style="left:173px"></span>
      <span class="pager-dot" style="left:194px"></span>
    </div>
  </div>
</section>

<h2 class="abs welcome-tab" style="font-weight:400">Welcome to our site</h2>
<div class="abs welcome-photo" role="img" aria-label="Photo of two smiling colleagues at a laptop"></div>
<p class="abs welcome-text">It is a long established fact that a reader will be distracted by the readable content of a page when looking at its layout. The point of using Lorem Ipsum is that it has a more-or-less normal distribution of letters, as opposed to using 'Content here, content here', making it look like readable English. Many desktop publishing packages and web page editors now use Lorem Ipsum as their default model text, and a search for 'lorem ipsum' will uncover many web sites still in their infancy. Various versions have evolved over the years, sometimes by accident, sometimes on purpose (injected humour and the like). <a href="#">View more</a></p>
<div class="abs rule"></div>

<h2 class="abs section-title" style="left:41px;top:715px;font-weight:400">Latest News</h2>
<div class="abs news-item" style="top:751px">
  <h4>The point of using is that it has a more</h4>
  <p>Many desktop publishing packages and web page editors now use default <a href="#">View more</a></p>
</div>
<div class="abs news-item" style="top:823px">
  <h4>The point of using is that it has a more</h4>
  <p>Many desktop publishing packages and web page editors now use default <a href="#">View more</a></p>
</div>
<div class="abs dash"></div>

<article class="abs feature" style="left:353px;width:213px">
  <h3>Video Demos</h3>
  <p class="lead">The point of using is that it has a more</p>
  <p class="body">Many desktop publishing packages and web page editors now use default <a href="#">View more</a></p>
  <div class="feature-icon" style="left:142px;background:linear-gradient(#eef3f8,#9fb8cf)" role="img" aria-label="Video clapper icon"></div>
</article>
<article class="abs feature" style="left:567px;width:219px;padding-left:24px">
  <h3>Easy Solutions</h3>
  <p class="lead">The point of using is that it has a more</p>
  <p class="body">Many desktop publishing packages and web page editors now use default <a href="#">View more</a></p>
  <div class="feature-icon" style="left:148px;background:linear-gradient(135deg,#6fb7e8,#e84040 55%,#5cc452)" role="img" aria-label="Stacked coloured cubes illustration"></div>
</article>
<article class="abs feature" style="left:787px;width:224px;padding-left:26px">
  <h3>Tools</h3>
  <p class="lead">The point of using is that it has a more</p>
  <p class="body">Many desktop publishing packages and web page editors now use default <a href="#">View more</a></p>
  <div class="feature-icon" style="left:158px;width:50px;background:linear-gradient(#d8d8d8,#8a8a8a)" role="img" aria-label="Wrench and hammer illustration"></div>
</article>

<h2 class="abs section-title" style="left:41px;top:907px;font-weight:400">Testimonials</h2>
<blockquote class="abs quote"><b>“</b> Passages are also reproduced in their exact original form, accompanied by English versions from the 1914 translation by J. Morrow. <b>”</b></blockquote>
<svg class="abs quote-tail" width="28" height="18" viewBox="0 0 28 18"><path d="M0 0H22L26 16Z" fill="#4b4b4b"/></svg>
<div class="abs quote-name">J. Morrow.</div>

<h2 class="abs block-title" style="left:362px;top:907px;font-weight:400">News Letter</h2>
<div class="abs mail-input">Enter mail ID</div>
<div class="abs subscribe">Subscribe</div>
<p class="abs mail-note">Passages are also reproduced in their exact original form</p>
<div class="abs v-rule"></div>

<h2 class="abs block-title" style="left:620px;top:907px;font-weight:400">Contact Us</h2>
<div class="abs contact-line" style="top:937px">
  <svg width="20" height="20" viewBox="0 0 20 20"><path d="M2 4H11M2 4V18H16V9" fill="none" stroke="#555" stroke-width="2"/><path d="M8 12L17 3" stroke="#555" stroke-width="2.5"/></svg>
  <span>Passages are also reproduced<br>exact original form<br>Accompanied</span>
</div>
<div class="abs contact-line" style="top:999px">
  <svg width="20" height="18" viewBox="0 0 20 18"><path d="M1 6C1 2 19 2 19 6V8H14V6H6V8H1Z" fill="#555"/><path d="M4 9H16L18 17H2Z" fill="#555"/><circle cx="10" cy="13" r="2" fill="#fff"/></svg>
  <span>456 321 7780</span>
</div>
<div class="abs contact-line" style="top:1031px">
  <svg width="20" height="16" viewBox="0 0 20 16"><rect x="1" y="3" width="17" height="11" fill="#666"/><path d="M1 3L9.5 9L18 3" fill="none" stroke="#ddd" stroke-width="1.2"/></svg>
  <span>info@zavora-platform.com</span>
</div>
<div class="abs social-art" role="img" aria-label="Illustration of a figure holding up a social media sign"></div>

<footer class="abs footer">
  <div class="footer-links">Home<span>|</span>Products<span>|</span>About Us<span>|</span>Pricing<span>|</span>Contactus<span>|</span>Sitemap</div>
  <div class="copyright">Copyright © 2011 www.zavora-platform.com &nbsp; All rights reserved</div>
</footer>

</body>
</html>
```